Logo and Website Design for QR.KA Horizon - a Software Engineering and IT company

Software engineering and IT are two different disciplines - and yet inseparably linked. At QR.KA Horizon, we combine both worlds and ensure that our software solutions are not only innovative and powerful, but also integrate perfectly into existing IT landscapes. Vision stands more for imagination, so it is not neccessary something what has to do with visualisation. Please consider that the winning competitor is also instructed to make a logo for the company. So please make a suitable logo for QR.KA Horizon to which the website fits to and show it during the website creation process. A good Logo desing is important for winning the competition. The website should contain a landing page with inspiring, perhaps futuristic photos of a datacenter and lines of code. Eventuelly flewent integrated in the text. On the landing page the company should introduced with a small text (max 250 words) followed by a section with a short text to one of our products nearby a graphic visualising the architecture of the product. The menue should be on top and fixed during scrolling and consist of the menue items home, solutions, who are we and a contact button. There should be a footer for linking social media, rights and Impressum. Only as an idea not a must. The very first view on the landing page could also be the menue bar and below of it a transparent unsharp photo (e.g. datacenter, lines of code, both ;) with the company name in the center.

###############################################################

Hi Designers,

Despite your very good approaches for describing QR.KA Horizon, here a short introduction (german text) from ourself:

------
QR.KA Horizon – Ihr Partner für ganzheitliche Softwarelösungen

Die QR.KA Horizon ist ein dynamisches Unternehmen, das sich nicht nur auf die Konzeption, das Design und die Entwicklung maßgeschneiderter Software spezialisiert hat, sondern auch deren reibungslosen Betrieb sicherstellt. Mit einem Team aus erfahrenen Softwarearchitekten und IT-Professionals verbinden wir modernste Softwareentwicklung mit tiefgehendem IT-Know-how – für Lösungen, die nachhaltig, leistungsstark und zukunftssicher sind.

Software Engineering trifft IT – Perfektion in Kombination
Software Engineering und IT sind zwei unterschiedliche Disziplinen – und doch untrennbar miteinander verbunden. Wir bei QR.KA Horizon vereinen beide Welten und sorgen dafür, dass unsere Softwarelösungen nicht nur innovativ und leistungsfähig sind, sondern sich auch perfekt in bestehende IT-Landschaften integrieren.

Expertise mit Fokus auf Healthcare & komplexe IT-Umgebungen
Unsere Experten bringen jahrzehntelange Erfahrung aus dem Healthcare-Sektor mit und unterstützen IT-Abteilungen großer Kliniken in der Entwicklung und Optimierung von Softwarelösungen. Von Anwendungssoftware bis hin zu Steuerungssystemen – unsere Softwareingenieure wissen genau, worauf es ankommt.

Ganzheitlicher Ansatz – über die Software hinaus
Wir entwickeln nicht nur Software, sondern übernehmen auch die Verantwortung für deren stabile und effiziente Betriebsumgebung. Egal, ob on-premises, in der Cloud oder als SaaS-Lösung – wir kümmern uns um den kompletten Lifecycle Ihrer Anwendung.

Ihre Vision – unsere Mission.
Ob Neuentwicklung einer SaaS-Anwendung oder die Migration bestehender Lösungen in eine moderne SaaS-Umgebung – mit QR.KA Horizon haben Sie einen starken Partner an Ihrer Seite.

Lassen Sie uns gemeinsam die Zukunft Ihrer Software gestalten!
--------------

Our first solution called "Clear Record Transfer Gateway" (CLURA)
-------------------
Teilen Sie Ihre Daten sicher – ohne Kompromisse!

Sie nutzen eine relationale Datenbank (Brightcask, Tabulon Hub, Vellumdb etc.) und möchten ausgewählte Daten mit Dritten teilen – sei es für ein Data Warehouse, Business Controller, Lieferanten oder Kunden? Doch dabei sollen Datensicherheit, Integrität und Verfügbarkeit Ihrer primären Lösung in keiner Weise gefährdet werden?

Mit unserer Lösung erhalten Sie genau das: Maximalen Schutz für Ihre Anwendung bei gleichzeitigem Nutzen durch autorisierte Dritte – ganz ohne teure Lizenzkosten für eine Schattendatenbank.

Lassen Sie uns gemeinsam herausfinden, wie Sie Ihre Daten sicher und effizient nutzen können. Kontaktieren Sie uns – wir zeigen Ihnen, was möglich ist!
---------------------

Our second solution MIVO:
---------------------
MIVO – Program for a Tone Matching Instrument ist die smarte Lösung für Unternehmen, die bei Farbgenauigkeit keine Kompromisse machen. Die Software erkennt Farbabweichungen zwischen Mustern vollautomatisch, beschreibt sie verständlich und sorgt so für gleichbleibend hohe Produktqualität – schnell, visuell und präzise. Perfekt für alle, die Farbe zur Vertrauenssache machen.
-------------------------

Thanks,
Gerold

Target Market(s)

IT Professionals from any sector

Industry/Entity Type

Healthcare and other

Coding

Coded - Design and coding required

Number of Pages Required

1 page

Font styles to use
Sans Serif

Colors
0054AA
0677BA
7BADD7
CADEEF
E8F1F8
0094D4
00A9DD
6FCCEA
C7EBF8
E9F6FB
00AB8E
00BBA5
67D7C9
C6EFE9
E9F9F6

Requirements
Must have
• Please see description
Nice to have
• On the landing page the company should introduced with a small text (max 250 words) followed by a section with a short text to one of our products nearby a graphic visualising the architecture of the product. The menue should be on top and fixed during scrolling and consist of the menue items home, solutions, who are we and a contact button. There should be a footer for linking social media, rights and Impressum. Only as an idea not a must. The very first view on the landing page could also be the menue bar and below of it a transparent unsharp photo (e.g. datacenter, lines of code, both ;) with the company name in the center.
Should not have
• Please see description

```html
<!DOCTYPE html>
<html lang="en">
<head>
<meta charset="utf-8">
<title>QR.KA Horizon – Software Engineering &amp; IT</title>
<link href="https://fonts.googleapis.com/css2?family=Lato:wght@400;600;700&display=swap" rel="stylesheet">
<style>
:root{
  --navy:#1d4c9a;
  --navy-dark:#163f85;
  --green:#00ab8e;
  --ink:#111;
  --text:#333;
  --pale:#e8f0fa;
  --white:#fff;
}
*{box-sizing:border-box;margin:0;padding:0}
html,body{width:1200px;height:2957px;overflow:hidden}
body{font-family:'Lato',sans-serif;color:var(--text);background:var(--white);position:relative}
.abs{position:absolute}
.btn{display:inline-flex;align-items:center;justify-content:center;border-radius:24px;font-weight:700;font-size:17px;text-decoration:none}
.btn-navy{background:var(--navy);color:#fff}
.btn-white{background:#fff;color:var(--navy)}
.accent{color:var(--green)}

/* header */
.topbar{left:519px;top:0;width:681px;height:46px;background:var(--navy);clip-path:polygon(0 0,100% 0,100% 100%,22px 100%,0 0)}
.topbar-item{top:10px;color:#fff;font-size:15px;display:flex;align-items:center;gap:10px;white-space:nowrap}
.social-top{top:13px;width:20px;height:20px;border:2px solid #fff;border-radius:3px}
.brand{display:flex;align-items:center;gap:10px;color:var(--ink);font-weight:700;white-space:nowrap}
.brand-mark{background:var(--navy)}
.nav{left:443px;top:68px;display:flex;gap:28px;font-size:16px;color:var(--ink)}
.nav a{color:var(--ink);text-decoration:none}
.nav a.active{color:var(--navy);text-decoration:underline}

/* hero */
.hero{left:0;top:115px;width:1200px;height:442px;background:radial-gradient(ellipse at 50% 45%,#2d5fb5 0%,#132f6e 45%,#07122e 100%)}
.hero h1{position:absolute;top:95px;width:100%;text-align:center;font-size:62px;color:#fff;font-weight:700;text-shadow:0 3px 6px rgba(0,0,0,.5)}
.hero p{position:absolute;left:354px;top:178px;width:470px;color:#fff;font-size:14.5px;line-height:29px}

/* about */
.section-h{font-size:38px;font-weight:700;color:var(--ink);line-height:1.35}
.body-txt{font-size:14.5px;line-height:29px;color:var(--text)}

/* innovative */
.band{left:0;top:1068px;width:1200px;height:585px;background:var(--pale)}
.ticks li{list-style:none;position:relative;padding-left:23px;font-size:14.5px;line-height:28px}
.ticks li::before{content:"";position:absolute;left:2px;top:11px;width:8px;height:8px;border-radius:50%;background:var(--navy)}

/* cards */
.card-img{width:311px;height:323px;border-radius:8px}
.card-title{width:340px;text-align:center;font-size:21px;color:var(--ink);font-weight:600}
.arrow{width:20px;height:26px}

/* cta */
.cta{left:0;top:2252px;width:1200px;height:359px;background:radial-gradient(ellipse at 50% 50%,#2553a6 0%,#1a468f 60%,#133a7c 100%)}
.cta h2{position:absolute;top:95px;width:100%;text-align:center;color:#fff;font-size:39px;font-weight:700}
.cta p{position:absolute;left:160px;top:165px;width:880px;text-align:center;color:#fff;font-size:14.5px;line-height:26px}

/* footer */
.foot-h{font-size:20px;color:var(--ink);font-weight:600}
.foot-list li{list-style:none;position:relative;padding-left:20px;font-size:15px;line-height:29px;color:var(--ink)}
.foot-list li::before{content:"";position:absolute;left:1px;top:11px;width:7px;height:7px;border-radius:50%;background:var(--navy)}
.contact-row{display:flex;gap:9px;font-size:15px;line-height:29px;color:var(--ink)}
.contact-row svg{flex:none;margin-top:7px}
.soc{display:flex;gap:10px;font-size:13px;color:var(--ink);font-weight:600}
.soc span{display:flex;align-items:center;gap:4px}
.soc i{width:12px;height:12px;border-radius:50%;background:var(--navy);display:block}
.rule{left:0;top:2903px;width:1200px;height:1px;background:#ccc}
</style>
</head>
<body>

<!-- header -->
<div class="abs topbar"></div>
<div class="abs topbar-item" style="left:566px">
  <svg width="26" height="26" viewBox="0 0 26 26"><rect width="26" height="26" rx="5" fill="#fff"/><path d="M8 6l3 0 1.5 4-2 1.5a9 9 0 004 4l1.5-2 4 1.5v3a2 2 0 01-2 2A13 13 0 016 8a2 2 0 012-2z" fill="#1d4c9a"/></svg>
  555.014.270</div>
<div class="abs topbar-item" style="left:718px">
  <svg width="26" height="26" viewBox="0 0 26 26"><rect width="26" height="26" rx="5" fill="#fff"/><rect x="5" y="8" width="16" height="11" fill="none" stroke="#1d4c9a" stroke-width="2"/><path d="M5 8l8 6 8-6" fill="none" stroke="#1d4c9a" stroke-width="2"/></svg>
  info@qrkahorizon.example</div>
<div class="abs social-top" style="left:964px" aria-label="Linkra"></div>
<div class="abs social-top" style="left:998px" aria-label="Chirpo"></div>
<div class="abs social-top" style="left:1033px" aria-label="Pixto"></div>
<div class="abs social-top" style="left:1067px" aria-label="Workly"></div>

<div class="abs brand" style="left:112px;top:30px;font-size:26px">
  <div class="brand-mark" style="width:42px;height:42px"></div>QR.KA Horizon</div>

<nav class="abs nav">
  <a class="active" href="#">Home</a><a href="#">Solutions</a><a href="#">Who Are We</a><a href="#">Testimonials</a>
</nav>
<a class="abs btn btn-navy" href="#" style="left:918px;top:58px;width:170px;height:44px">Contact Us</a>

<!-- hero -->
<section class="abs hero" role="img" aria-label="Blurred photo of a data centre corridor lined with glowing server racks">
  <h1>QR.KA Horizon</h1>
  <p>At QR.KA Horizon, we blend the best of software engineering and IT to deliver cutting-edge solutions that power your business forward.</p>
  <a class="btn btn-white" href="#" style="position:absolute;left:515px;top:266px;width:170px;height:44px">Get Started</a>
</section>

<!-- about -->
<h2 class="abs section-h" style="left:110px;top:650px">About <span class="accent">QR.KA Horizon</span></h2>
<p class="abs body-txt" style="left:110px;top:710px;width:420px">At QR.KA Horizon, we are driven by the belief that the future of technology lies in the seamless integration of software engineering and IT. Founded with a vision to bridge the gap between these two powerful fields, we specialize in creating innovative, forward-thinking software solutions that integrate effortlessly into existing IT landscapes.</p>
<a class="abs btn btn-navy" href="#" style="left:110px;top:902px;width:170px;height:44px">Read More</a>
<div class="abs" style="left:608px;top:650px;width:489px;height:331px;background:var(--green)"></div>
<div class="abs" role="img" aria-label="Photo of two engineers studying holographic code displays" style="left:599px;top:641px;width:489px;height:331px;background:linear-gradient(135deg,#0c3a5c,#1e6f9a 45%,#0a2440)"></div>

<!-- innovative -->
<div class="abs band"></div>
<div class="abs" style="left:101px;top:1161px;width:449px;height:406px;background:var(--green)"></div>
<div class="abs" role="img" aria-label="Illustration of a server hall with a glowing cloud symbol" style="left:110px;top:1152px;width:449px;height:406px;background:radial-gradient(ellipse at 50% 50%,#19c4e6 0%,#0d5b86 35%,#07213d 100%)"></div>
<h2 class="abs section-h" style="left:640px;top:1140px;width:440px;line-height:52px">Innovative Software Solutions for a <span class="accent">Seamless IT Experience</span></h2>
<p class="abs body-txt" style="left:640px;top:1300px;width:445px;line-height:26px">At QR.KA Horizon, we specialize in developing cutting-edge software solutions designed to transform and optimize your IT infrastructure. Our products are crafted with the future in mind,</p>
<ul class="abs ticks" style="left:640px;top:1390px">
  <li>Enhance Performance</li><li>Seamlessly Integrate</li><li>Scale with Your Needs</li><li>Future-Proof Your Systems</li>
</ul>
<a class="abs btn btn-navy" href="#" style="left:642px;top:1519px;width:170px;height:44px">Read More</a>

<!-- empowering -->
<h2 class="abs section-h" style="left:0;top:1726px;width:1200px;text-align:center">Empowering Your Business with <span class="accent">Seamless IT Integration</span></h2>
<svg class="abs arrow" style="left:44px;top:1960px" viewBox="0 0 20 26"><path d="M14 3L5 13l9 10" fill="none" stroke="#111" stroke-width="3"/></svg>
<svg class="abs arrow" style="left:1130px;top:1960px" viewBox="0 0 20 26"><path d="M6 3l9 10-9 10" fill="none" stroke="#555" stroke-width="2.5"/></svg>

<div class="abs card-img" role="img" aria-label="Photo of a blue-lit server corridor" style="left:111px;top:1802px;background:linear-gradient(180deg,#0b1f4a,#1659c6 60%,#0a2a6a)"></div>
<div class="abs card-img" role="img" aria-label="Photo of a hand holding a glowing compliance document icon above a laptop" style="left:444px;top:1802px;background:radial-gradient(circle at 40% 45%,#f08a2a 0%,#6b3a1f 35%,#1b1b22 80%)"></div>
<div class="abs card-img" role="img" aria-label="Illustration of a glowing cloud inside a server room" style="left:776px;top:1802px;background:radial-gradient(ellipse at 50% 35%,#3fd3ee 0%,#0e5a85 40%,#0a1d33 100%)"></div>
<div class="abs card-title" style="left:96px;top:2146px">IT Infrastructure Optimization</div>
<div class="abs card-title" style="left:429px;top:2146px">Data Security &amp; Compliance</div>
<div class="abs card-title" style="left:762px;top:2146px">Cloud Integration &amp; Migration</div>

<!-- cta -->
<section class="abs cta" role="img" aria-label="Blue background with faint streams of binary digits">
  <h2>Let's Build the Future Together</h2>
  <p>We're excited to learn more about your business and discuss how QR.KA Horizon can help you optimize your IT landscape and achieve your goals. Whether you have a question, need a consultation, or want to explore our solutions further, we are here to help.</p>
  <a class="btn btn-white" href="#" style="position:absolute;left:515px;top:234px;width:170px;height:44px">Get Started</a>
</section>

<!-- footer -->
<div class="abs" style="left:111px;top:2670px;width:60px;height:60px;background:var(--navy)"></div>
<div class="abs brand" style="left:110px;top:2770px;font-size:27px">QR.KA Horizon</div>
<div class="abs soc" style="left:110px;top:2825px">
  <span><i></i>Linkra</span><span><i></i>Pixto</span><span><i></i>Chirpo</span><span><i></i>Workly</span>
</div>

<div class="abs foot-h" style="left:350px;top:2692px">Quick Links</div>
<ul class="abs foot-list" style="left:350px;top:2722px"><li>Home</li><li>Solutions</li><li>Who Are We</li></ul>

<div class="abs foot-h" style="left:557px;top:2690px">Legal Information</div>
<ul class="abs foot-list" style="left:557px;top:2720px"><li>Impressum</li><li>Privacy Policy</li><li>Terms and Use</li></ul>

<div class="abs foot-h" style="left:814px;top:2692px">Contact Us</div>
<div class="abs" style="left:814px;top:2722px;width:290px">
  <div class="contact-row"><svg width="16" height="16" viewBox="0 0 16 16"><circle cx="8" cy="8" r="8" fill="#1d4c9a"/><path d="M5 4h2l1 2.5-1.2 1a5 5 0 002.5 2.5l1-1.2L12.8 10v2a1 1 0 01-1 1A8 8 0 014 5a1 1 0 011-1z" fill="#fff"/></svg>+555 014 270</div>
  <div class="contact-row"><svg width="16" height="16" viewBox="0 0 16 16"><circle cx="8" cy="8" r="8" fill="#1d4c9a"/><rect x="4" y="5.5" width="8" height="5.5" fill="none" stroke="#fff" stroke-width="1.2"/><path d="M4 5.5l4 3 4-3" fill="none" stroke="#fff" stroke-width="1.2"/></svg>hello@qrkahorizon.example</div>
  <div class="contact-row"><svg width="16" height="16" viewBox="0 0 16 16"><path d="M8 0a6 6 0 016 6c0 4.5-6 10-6 10S2 10.5 2 6a6 6 0 016-6z" fill="#1d4c9a"/><circle cx="8" cy="6" r="2.3" fill="#fff"/></svg>QR.KA Horizon HQ&nbsp; 48 Meridian Lane, Harbor Vale, NV 40217 United States</div>
</div>

<div class="abs rule"></div>
<div class="abs" style="left:0;top:2922px;width:1200px;text-align:center;font-size:15px;color:var(--ink)">2025 © QR.KA Horizon. All rights Reserved.</div>

</body>
</html>
```